Book Cover for a book on Quiet Ventures

I am self-publishing my book on Brindlecart and need a book cover made. Below are the details. See attached templates for size we need to use. I also attached a previous cover we had made that I liked. The problem with it was they were two boys helping each other but the book is about women. I'm open to your ideas on the cover though, but I wanted to show you a style I liked as an idea.
Front of Cover
Book Title: Quiet Ventures
Book Subtitle: Raw Reflections of a Female CEO
Author Name: Lorna T. Pelham
Add on the Spine of Cover: Quiet Ventures and Lorna T. Pelham
Back of the Cover Text:
Quiet Ventures: Unvarnished Notes of a Woman Founder is an honest account of a business owner’s experience attempting to navigate the start-up community while also pursuing spiritual growth. Author Lorna Pelham defines a spiritual entrepreneur as “someone who runs an enterprise with the purpose of growing love rather than material gain.” This book discusses the three dimensions of Quiet Ventures:
1. The business is an integral part of the founder’s spiritual journey.
2. Employees working for the spiritual enterprise, whether they know it or not, encounter this company because it's part of their spiritual path.
3. The business itself has a life force of its own and its purpose is to further the kingdom of heaven on earth.
These three dimensions happen simultaneously and work together to produce the greatest possible result. However, this can feel confusing to a founder juggling these dimensions while also trying to manage and run a business. This is not a formulaic self-help book or roadmap. Rather, it is a compilation of personal reflections that often seem at odds with the traditional world of entrepreneurship.
Below the description add my picture (see attached for my picture)
Bio text:
Lorna Pelham founded Halvex with the vision of ushering in a life-long education system that shifts away from standardization to one that empowers people to live their purpose. In college, Lorna interned for Open Meadow, a women’s empowerment initiative where she recognized her passion for helping people find their voice. Lorna's 20-year journey has come full circle to empowering other female CEOs who are pursuing the path of Quiet Ventures.
NOTE: Please note that Brindlecart puts a bar code on the bottom right of the back cover as is noted on the attached template.
Size template is attached to the brief, here are the sizes typed out:
# Description Width (in) Height (in)
1 Full Cover 12.79 9.25
2 Front Cover 6 9
3 Safe Area 5.875 8.75
4 Bleed 0.125 0.125
5 Margin 0.125 0.125
6 Spine 0.54 9
7 Spine Safe Area 0.415 8.75
8 Spine Margin 0.062 0.062
9 Barcode Margin 0.25 0.25
Pre-publication checklist
BRINDLECART TIPS for the final cover:
1. Save as a PDF. Your cover must be a single PDF that includes the back cover, spine, and front cover as one image.
2. Flatten all transparencies. These can cause the file to print with missing or distorted content. Consult your software's documentation to learn how.
3. Embed your fonts. Consult your software's documentation to learn how.
4. Remove crop marks, color bars, template text. Crop marks are lines showing where pages should be trimmed. Color bars are strips with a series of patches used to ensure color balance during printing. Also, remove any template text, PDF creation guides, or software references.
5. Ensure your cover image meets the minimum resolution of 300 DPI (dots per inch).
6. Optimize PDFs. Optimization is useful to reduce your file size, allowing for higher performance when transferring, uploading, viewing, and printing the files.
7. Remove file security. Locked or encrypted files will fail review.
Target Market(s)
Women who want to be CEOs or are currently CEOs of companies.
Industry/Entity Type
Entrepreneurship, business, spirituality
Requirements
Must have
- Just the text on the description. A very welcoming feel.
Nice to have
- I like the idea of having a sunrise/sunset in the image somehow like in the example I attached to the brief, but again I'm open.
Should not have
- Please don't put any yoga or meditation poses or hands outstretched. I have a lot of interesting ones that look like my example so if you are going to submit after Saturday 10/29, please only do so if you have a new idea! Thanks!

```html
<!DOCTYPE html>
<html lang="en">
<head>
<meta charset="utf-8">
<title>Quiet Ventures — Book Cover</title>
<link rel="stylesheet" href="https://fonts.googleapis.com/css2?family=Libre+Caslon+Text:ital,wght@0,400;0,700;1,400&family=Source+Sans+3:wght@400;600&display=swap">
<style>
  :root{
    --bg:#e9e9e9;
    --paper:#ffffff;
    --ink:#1f1f1f;
    --title:#2a2a2a;
    --accent:#e8501e;
    --photo-a:#f2f1ef;
    --photo-b:#d9d6d2;
    --author-a:#8a5a44;
    --author-b:#c7a48c;
  }
  *{box-sizing:border-box;margin:0;padding:0}
  html,body{width:847px;height:1200px;overflow:hidden;background:var(--bg)}
  .canvas{position:relative;width:847px;height:1200px}
  .spread{
    position:absolute;left:0;top:294px;width:847px;height:613px;
    display:flex;background:var(--paper);
    box-shadow:0 2px 10px rgba(0,0,0,.12);
  }
  /* Back cover */
  .back{position:relative;width:405px;height:100%;background:var(--paper);
    font-family:"Libre Caslon Text",Georgia,serif;color:var(--ink)}
  .back-copy{position:absolute;left:22px;top:24px;right:22px;font-size:8.6px;line-height:1.42}
  .back-copy p{margin-bottom:7px}
  .back-copy ol{margin:0 0 7px 16px}
  .back-copy li{margin-bottom:2px}
  .bio{position:absolute;left:22px;right:22px;top:356px;display:flex;gap:10px}
  .bio-photo{flex:0 0 64px;height:74px;background:linear-gradient(160deg,var(--author-b),var(--author-a))}
  .bio-text{font-size:8.4px;line-height:1.42}
  .bio-text strong{font-weight:700}
  .imprint{position:absolute;left:22px;bottom:70px;
    font-family:"Source Sans 3",Arial,sans-serif;font-size:13px;font-weight:600;color:var(--ink);
    display:flex;align-items:center;gap:6px;line-height:1}
  .imprint-mark{width:10px;height:10px;background:var(--ink)}
  .band{position:absolute;left:0;right:0;bottom:0;height:52px;background:var(--accent)}
  /* Spine */
  .spine{position:relative;width:37px;height:100%;background:var(--paper);
    border-left:1px solid #efefef;border-right:1px solid #efefef}
  .spine-text{position:absolute;left:50%;top:22px;transform-origin:0 0;
    transform:rotate(90deg) translateY(-50%);white-space:nowrap;
    font-family:"Libre Caslon Text",Georgia,serif;font-size:14px;color:var(--title);
    display:flex;gap:120px;width:480px}
  .spine-author{font-size:11px;padding-top:3px}
  /* Front cover */
  .front{position:relative;width:405px;height:100%;background:var(--paper);
    font-family:"Libre Caslon Text",Georgia,serif}
  .front-photo{position:absolute;left:0;top:0;width:100%;height:372px;
    background:linear-gradient(180deg,var(--photo-a) 0%,var(--photo-b) 100%)}
  .title{position:absolute;left:0;right:0;top:392px;text-align:center;
    font-size:35px;font-weight:400;line-height:1.12;color:var(--title)}
  .subtitle{position:absolute;left:0;right:0;top:480px;text-align:center;
    font-style:italic;font-size:18px;color:var(--title)}
  .author{position:absolute;left:0;right:0;bottom:0;height:60px;background:var(--accent);
    color:#fff;font-size:20px;display:flex;align-items:center;justify-content:center}
</style>
</head>
<body>
<div class="canvas">
  <div class="spread">
    <section class="back">
      <div class="back-copy">
        <p><em>Quiet Ventures: Unvarnished Notes of a Woman Founder</em> is an honest account of a business owner’s experience attempting to navigate the start-up community while also pursuing spiritual growth. Author Lorna Pelham defines a spiritual entrepreneur as “someone who runs an enterprise with the purpose of growing love rather than material gain.” This book discusses the three dimensions of Quiet Ventures:</p>
        <ol>
          <li>The business is an integral part of the founder’s spiritual journey.</li>
          <li>Employees working for the spiritual enterprise, whether they know it or not, encounter this company because it's part of their spiritual path.</li>
          <li>The business itself has a life force of its own and its purpose is to further the kingdom of heaven on earth.</li>
        </ol>
        <p>These three dimensions happen simultaneously and work together to produce the greatest possible result. However, this can feel confusing to a founder juggling these dimensions while also trying to manage and run a business. This is not a formulaic self-help book or roadmap. Rather, it is a compilation of personal reflections that often seem at odds with the traditional world of entrepreneurship.</p>
      </div>
      <div class="bio">
        <div class="bio-photo" role="img" aria-label="Portrait photo of the author"></div>
        <p class="bio-text"><strong>Lorna Pelham</strong> founded Halvex with the vision of ushering in a life-long education system that shifts away from standardization to one that empowers people to live their purpose. In college, Lorna interned for Open Meadow, a women’s empowerment initiative where she recognized her passion for helping people find their voice. Lorna's 20-year journey has come full circle to empowering other female CEOs who are pursuing the path of Quiet Ventures.</p>
      </div>
      <div class="imprint"><span class="imprint-mark"></span>Brindlecart press</div>
      <div class="band"></div>
    </section>

    <section class="spine">
      <div class="spine-text">
        <span>Quiet Ventures</span>
        <span class="spine-author">Lorna T. Pelham</span>
      </div>
      <div class="band"></div>
    </section>

    <section class="front">
      <div class="front-photo" role="img" aria-label="Photo of a smiling woman sitting with a laptop against a soft light backdrop"></div>
      <h1 class="title">Quiet<br>Ventures</h1>
      <p class="subtitle">Raw Reflections of a Female CEO</p>
      <div class="author">Lorna T. Pelham</div>
    </section>
  </div>
</div>
</body>
</html>
```